Postcard design to acquire new clients for my Property Management Company

I'm looking for a postcard design that I can send to prospective clients detailing information about my company and services.
Postcard should be eye catching and contain information from www.bramblecrestpm.com. I've provided a few screen shots for the most important information and my logo.
Target Market(s)
Real Estate
Industry/Entity Type
Real Estate
Font styles to use
Sans Serif
Requirements
Must have
- Must be eye catching!! this will be a direct mail piece - I'd like for the card to be read and not tossed in the trash immediately.
Design que from the logo.
A place to write / print the receipts name and address.
our physical address - 2387 Hollow Pine Road, Lubbock, TX 79852.
Should not have
- the contact information on the business card is not accurate - please use info from website.

```html
<!DOCTYPE html>
<html lang="en">
<head>
<meta charset="utf-8">
<title>Bramblecrest Property Management Postcard</title>
<link href="https://fonts.googleapis.com/css2?family=Bebas+Neue&family=Montserrat:wght@500;600;700&family=Raleway:wght@500;600&family=Cormorant+Garamond:wght@500&display=swap" rel="stylesheet">
<style>
  :root {
    --page-bg: #e6e6e8;
    --navy: #0c3a73;
    --band: #04386a;
    --stripe: #0b5c97;
    --white: #ffffff;
    --ink: #111418;
    --grey-text: #9b9ca1;
  }
  * { box-sizing: border-box; margin: 0; padding: 0; }
  html, body { width: 857px; height: 1200px; overflow: hidden; }
  body { background: var(--page-bg); position: relative; font-family: "Raleway", sans-serif; color: var(--ink); }

  .side-label {
    position: absolute; left: 0; width: 857px; text-align: center;
    font-family: "Cormorant Garamond", serif; font-weight: 500;
    font-size: 27px; letter-spacing: 2px; color: var(--ink);
  }
  .side-label--front { top: 53px; }
  .side-label--back { top: 644px; }

  .card { position: absolute; left: 71px; width: 715px; height: 506px; background: var(--white); overflow: hidden; }
  .card--front { top: 94px; }
  .card--back { top: 676px; }

  .hero { position: absolute; left: 0; top: 0; width: 715px; height: 289px; }
  .hero--front { background: linear-gradient(100deg, #0d3a76 0%, #0f3f80 45%, #123f79 70%, #0c356a 100%); }
  .hero--back { background: linear-gradient(180deg, #a9cdeb 0%, #c4dcef 45%, #d8c7bd 75%, #cfd3d8 100%); }

  .hero-photo { position: absolute; }
  .hero--front .building-photo { left: 30px; top: 90px; width: 520px; height: 199px;
    background: linear-gradient(180deg, rgba(20,60,120,0) 0%, rgba(22,62,118,.7) 40%, rgba(10,40,85,.8) 100%); }
  .hero--back .building-photo { left: 283px; top: 80px; width: 300px; height: 209px;
    background: linear-gradient(180deg, #e9e7e4 0%, #d2a58e 45%, #f1efec 75%, #c9cdd2 100%); opacity: .85; }

  .portrait { left: 451px; width: 246px; height: 268px; bottom: 0;
    background: linear-gradient(180deg, rgba(60,66,78,0) 0%, #4b505b 45%, #2e323a 100%); border-radius: 110px 110px 0 0; }

  .headline { position: absolute; font-family: "Bebas Neue", sans-serif; font-weight: 400; color: var(--white); text-transform: uppercase; line-height: 1; }
  .headline span { position: absolute; left: 0; white-space: nowrap; }

  .front-headline { left: 69px; top: 0; width: 222px; height: 170px; }
  .front-headline .l1 { top: 8px;  font-size: 44px; }
  .front-headline .l2 { top: 58px; font-size: 34px; }
  .front-headline .l3 { top: 96px; font-size: 27px; }
  .front-headline .l4 { top: 132px; font-size: 33px; }

  .phone-block { position: absolute; font-family: "Bebas Neue", sans-serif; color: var(--white); text-align: center; white-space: nowrap; }
  .card--front .phone-block { left: 69px; width: 214px; top: 185px; height: 57px; font-size: 37px; line-height: 56px; letter-spacing: 2px;
    border-top: 1.5px solid var(--white); border-bottom: 1.5px solid var(--white); }

  .thumbs { position: absolute; left: 69px; top: 256px; display: flex; gap: 10px; }
  .thumb { width: 101px; height: 68px; background: var(--white); padding: 4px 5px 0; }
  .thumb-photo { width: 100%; height: 60px; border-bottom: 3px solid var(--navy); }
  .thumb-photo--villa { background: linear-gradient(180deg, #7fb2e2 0%, #d9d2c4 50%, #6c9a48 80%, #cfcfcf 100%); }
  .thumb-photo--tower { background: linear-gradient(180deg, #2e73c7 0%, #f1f1f1 45%, #3c3c3c 75%, #6d8a50 100%); }

  .brand-band { position: absolute; right: 0; top: 249px; width: 227px; height: 40px; }
  .brand-band svg { position: absolute; inset: 0; }
  .brand-name { position: absolute; right: 8px; top: 6px; font-family: "Montserrat", sans-serif; font-weight: 700; font-size: 16px; letter-spacing: 3.2px; color: var(--white); white-space: nowrap; }
  .brand-sub { position: absolute; right: 8px; top: 26px; font-family: "Montserrat", sans-serif; font-weight: 700; font-size: 8.6px; letter-spacing: 2.2px; color: var(--white); white-space: nowrap; }

  .bottom-stripe { position: absolute; left: 0; bottom: 0; width: 715px; height: 12px; background: var(--stripe); }

  .service { position: absolute; font-size: 8.6px; line-height: 11.5px; font-weight: 500; color: var(--ink); }
  .service h3 { display: inline; font-family: "Montserrat", sans-serif; font-weight: 700; font-size: 12.5px; letter-spacing: .4px; margin-right: 3px; text-transform: uppercase; }
  .service--left { left: 11px; width: 373px; text-align: justify; }
  .service--right { left: 394px; width: 312px; }

  .choose-panel { position: absolute; left: 69px; top: 0; width: 214px; height: 255px; background: var(--navy); }
  .back-headline { left: 15px; top: 0; width: 190px; height: 160px; }
  .back-headline .big { top: 15px; font-size: 64px; letter-spacing: 6px; }
  .back-headline .sub1 { top: 75px; font-size: 26px; letter-spacing: .8px; }
  .back-headline .sub2 { top: 102px; font-size: 26px; letter-spacing: .8px; }
  .contact-expert { position: absolute; left: 15px; top: 164px; font-family: "Bebas Neue", sans-serif; font-size: 35px; line-height: 1; color: var(--white); letter-spacing: .3px; white-space: nowrap; }
  .contact-rule { position: absolute; left: 15px; top: 205px; width: 185px; border-top: 1.5px solid var(--white); }
  .card--back .phone-block { left: 15px; width: 185px; top: 208px; height: 40px; font-size: 34px; line-height: 40px; letter-spacing: 1.2px; border-bottom: 1.5px solid var(--white); }

  .region-text { position: absolute; left: 20px; top: 341px; font-family: "Bebas Neue", sans-serif; font-size: 30px; line-height: 29px; color: var(--grey-text); letter-spacing: 1.7px; text-transform: uppercase; white-space: nowrap; }
  .fit-text { position: absolute; left: 20px; top: 411px; font-family: "Bebas Neue", sans-serif; font-size: 30px; line-height: 28.5px; color: var(--grey-text); letter-spacing: 1.7px; text-transform: uppercase; white-space: nowrap; }
  .fit-text .accent { color: var(--navy); }

  .return-address { position: absolute; left: 405px; top: 298px; font-family: "Montserrat", sans-serif; font-size: 11.3px; line-height: 14px; font-weight: 500; font-style: normal; }
  .return-address .email { font-size: 10px; }
  .stamp-box { position: absolute; left: 619px; top: 300px; width: 82px; height: 98px; border: 1px solid var(--ink); }
  .address-line { position: absolute; left: 405px; border-top: 1px solid var(--ink); }
  .address-line--1 { top: 398px; width: 194px; }
  .address-line--2 { top: 435px; width: 296px; }
  .address-line--3 { top: 471px; width: 296px; }
</style>
</head>
<body>

  <div class="side-label side-label--front">FRONT</div>

  <section class="card card--front">
    <div class="hero hero--front">
      <div class="hero-photo building-photo" role="img" aria-label="Modern rental building tinted in blue"></div>
      <div class="hero-photo portrait" role="img" aria-label="Portrait of the property manager in a dark suit"></div>

      <h1 class="headline front-headline">
        <span class="l1">Maximize your</span>
        <span class="l2">Financial returns</span>
        <span class="l3">with support from our</span>
        <span class="l4">Rental specialists</span>
      </h1>
      <div class="phone-block">(806)-555-0142</div>

      <div class="brand-band">
        <svg width="227" height="40" viewBox="0 0 227 40"><polygon points="30,0 227,0 227,40 0,40" fill="var(--band)"/></svg>
        <div class="brand-name">BRAMBLECREST</div>
        <div class="brand-sub">PROPERTY MANAGEMENT</div>
      </div>
    </div>

    <div class="thumbs">
      <div class="thumb"><div class="thumb-photo thumb-photo--villa" role="img" aria-label="Single-family villa with garden"></div></div>
      <div class="thumb"><div class="thumb-photo thumb-photo--tower" role="img" aria-label="White modern apartment building"></div></div>
    </div>

    <div class="service service--left" style="top:333px"><h3>Property Marketing</h3>Tired of waiting for weeks on end, hoping to find a new tenant? Let us take over your marketing for you and we'll find a qualified renter quickly.</div>
    <div class="service service--left" style="top:375px"><h3>Tenant Screening</h3>We don't just find someone to rent your home—we find the best renters. We screen all applications using fair housing guidelines to protect you.</div>
    <div class="service service--left" style="top:424px"><h3>Property Inspections</h3>Inspections form an important part of our proactive property management approach. We visit every home in our portfolio regularly.</div>
    <div class="service service--left" style="top:464px"><h3>Evictions</h3>When things go wrong inside your rental home, rest easy with the experts on your side. We will handle evictions for you &amp; find new renters when its over.</div>

    <div class="service service--right" style="top:307px"><h3>Legal Guidance</h3>Don't accidentally violate one of the many ordinances and housing laws governing your relationship with your tenants. Let us keep you compliant.</div>
    <div class="service service--right" style="top:355px"><h3>Rent Collection</h3>Stop guessing when you'll receive your rental earnings every month and say hello to consistent payments. We keep your tenants current.</div>
    <div class="service service--right" style="top:404px"><h3>Maintenance</h3>Still scrambling to respond to repair requests every time you receive a tenant call? Let us coordinate repair work on your behalf!</div>
    <div class="service service--right" style="top:453px"><h3>Financial Reporting</h3>Keep a handle on your real estate performance. We generate monthly statements so you can review income &amp; expenses at a moment's notice.</div>

    <div class="bottom-stripe"></div>
  </section>

  <div class="side-label side-label--back">BACK</div>

  <section class="card card--back">
    <div class="hero hero--back">
      <div class="hero-photo building-photo" role="img" aria-label="Modern white and brick house under a blue sky"></div>
      <div class="hero-photo portrait" role="img" aria-label="Portrait of the property manager in a dark suit"></div>

      <div class="choose-panel">
        <h2 class="headline back-headline">
          <span class="big">Choose</span>
          <span class="sub1">The right property</span>
          <span class="sub2">management system</span>
        </h2>
        <div class="contact-expert">CONTACT EXPERT</div>
        <div class="contact-rule"></div>
        <div class="phone-block">(806)-555-0142</div>
      </div>

      <div class="brand-band">
        <svg width="227" height="40" viewBox="0 0 227 40"><polygon points="30,0 227,0 227,40 0,40" fill="var(--band)"/></svg>
        <div class="brand-name">BRAMBLECREST</div>
        <div class="brand-sub">PROPERTY MANAGEMENT</div>
      </div>
    </div>

    <div class="thumbs">
      <div class="thumb"><div class="thumb-photo thumb-photo--villa" role="img" aria-label="Single-family villa with garden"></div></div>
      <div class="thumb"><div class="thumb-photo thumb-photo--tower" role="img" aria-label="White modern apartment building"></div></div>
    </div>

    <p class="region-text">Property management<br>across Lubbock, TX</p>
    <p class="fit-text">Not sure if! <span class="accent">Property</span><br><span class="accent">management is the right fit?</span><br>We'll help you figure it out.</p>

    <address class="return-address">2387 Hollow Pine Road,<br>Lubbock, TX 79852<br><span class="email">info@bramblecrestpm.com</span></address>
    <div class="stamp-box"></div>
    <div class="address-line address-line--1"></div>
    <div class="address-line address-line--2"></div>
    <div class="address-line address-line--3"></div>
  </section>

</body>
</html>
```